The design should look similar to the uploaded example to accommodate the information needed for a business card template. I would like to see the colors orange and charcoal grey incorporated along with the logo.The following should be on the back of the card SPECIALIZING IN NEW AND USED TIRES & WHEELS FOR:- Loaders- Skid Steers- Telehandlers- Boom Lifts- Forklifs and moreELIMINATING DOWNTIMEWheel Exchange Program for New & Used Foam Filled and Solid Rubber TiresSPECIALTY SERVICES- Foam Filling Tires- Largest Tire Press in SE- ONSITE Forklift Tire Press- Boom Truck Services - Rubber Tracks

Target Market(s)

New and Existing Customers

Industry/Entity Type

Business

Contact Information for Business Card

NAMEHEAVY DUTY TIRE, LLC8470 Belvedere RoadWest Palm Beach, FL 33411P: 844-HD-TIRESF: 561-431-6469C:E: W: WWW.GRANITERIMSUPPLY-EXAMPLE.COM

Font styles to use
Sans Serif

Colors
f37122
333333

Requirements
Must have
• The logo and the information indicated for the backside of the card
Nice to have
• Keep the orange and charcoal grey colors

```html
<!DOCTYPE html>
<html lang="en">
<head>
<meta charset="utf-8">
<title>Granite Rim Supply – Business Card</title>
<link rel="stylesheet" href="https://fonts.googleapis.com/css2?family=Open+Sans:wght@400;600;700&display=swap">
<style>
  :root {
    --orange: #f58634;
    --charcoal: #3a4040;
    --white: #ffffff;
    --backdrop: #e9e7e4;
  }
  html, body {
    margin: 0;
    width: 1200px;
    height: 900px;
    overflow: hidden;
    background: var(--backdrop);
    font-family: "Open Sans", sans-serif;
  }
  .card {
    position: absolute;
    left: 100px;
    top: 140px;
    width: 1000px;
    height: 620px;
    background: var(--white);
    overflow: hidden;
  }
  .card-wave {
    position: absolute;
    inset: 0;
    width: 100%;
    height: 100%;
  }
  .brand-mark {
    position: absolute;
    left: 99px;
    top: 84px;
    width: 330px;
    height: 330px;
    border-radius: 50%;
    background: var(--charcoal);
    display: flex;
    align-items: center;
    justify-content: center;
    text-align: center;
  }
  .brand-name {
    color: var(--orange);
    font-weight: 700;
    font-size: 52px;
    line-height: 1.05;
    letter-spacing: 1px;
  }
  .holder-name {
    position: absolute;
    right: 49px;
    top: 50px;
    margin: 0;
    color: var(--orange);
    font-weight: 600;
    font-size: 37px;
  }
  .contact-list {
    position: absolute;
    right: 46px;
    top: 280px;
    margin: 0;
    padding: 0;
    list-style: none;
    color: var(--white);
    font-size: 24px;
  }
  .contact-item {
    display: flex;
    align-items: center;
    justify-content: flex-end;
    height: 41.5px;
  }
  .contact-icon {
    width: 20px;
    height: 20px;
    margin-left: 16px;
    fill: var(--white);
  }
  .company {
    position: absolute;
    right: 50px;
    top: 505px;
    margin: 0;
    color: var(--white);
    font-weight: 600;
    font-size: 29px;
  }
  .address {
    position: absolute;
    right: 50px;
    top: 552px;
    margin: 0;
    color: var(--white);
    font-size: 26px;
  }
</style>
</head>
<body>
  <article class="card">
    <svg class="card-wave" viewBox="0 0 652 404" preserveAspectRatio="none" aria-hidden="true">
      <path d="M0,222 C80,290 140,332 210,328 C320,322 420,205 520,168 C580,148 625,150 652,164 L652,404 L0,404 Z" fill="var(--orange)"/>
      <path d="M0,210 C70,272 130,318 200,314 C310,308 400,170 510,122 C575,96 625,115 652,150" fill="none" stroke="var(--charcoal)" stroke-width="11"/>
    </svg>

    <div class="brand-mark">
      <span class="brand-name">GRANITE<br>RIM</span>
    </div>

    <h1 class="holder-name">Marcus Delaney</h1>

    <ul class="contact-list">
      <li class="contact-item">844-GR-WHEEL
        <svg class="contact-icon" viewBox="0 0 24 24"><path d="M6.6 10.8a15.1 15.1 0 0 0 6.6 6.6l2.2-2.2a1 1 0 0 1 1-.25 11.4 11.4 0 0 0 3.6.57 1 1 0 0 1 1 1V20a1 1 0 0 1-1 1A17 17 0 0 1 3 4a1 1 0 0 1 1-1h3.5a1 1 0 0 1 1 1c0 1.25.2 2.450.57 3.57a1 1 0 0 1-.25 1z"/></svg>
      </li>
      <li class="contact-item">561-278-9053
        <svg class="contact-icon" viewBox="0 0 24 24"><path d="M7 3h8l3 3v4H7zM4 11h16a2 2 0 0 1 2 2v7H2v-7a2 2 0 0 1 2-2zm3 3v2h3v-2zm5 0v2h3v-2z"/></svg>
      </li>
      <li class="contact-item">561-390-7724
        <svg class="contact-icon" viewBox="0 0 24 24"><path d="M7 1h10a2 2 0 0 1 2 2v18a2 2 0 0 1-2 2H7a2 2 0 0 1-2-2V3a2 2 0 0 1 2-2zm0 3v14h10V4z"/></svg>
      </li>
      <li class="contact-item">info@graniterim-example.com
        <svg class="contact-icon" viewBox="0 0 24 24"><path d="M2 5h20v14H2zm2 2v.4l8 5.2 8-5.2V7zm0 2.8V17h16V9.8l-8 5.2z"/></svg>
      </li>
      <li class="contact-item">www.graniterimsupply-example.com
        <svg class="contact-icon" viewBox="0 0 24 24"><circle cx="12" cy="12" r="10"/></svg>
      </li>
    </ul>

    <p class="company">GRANITE RIM SUPPLY, LLC</p>
    <p class="address">5126 Marston Lane Cedar Hollow, FL 33488</p>
  </article>
</body>
</html>
```